Website mockup using figma or other design software for Plumbing Company

We are looking for a talented UI/UX designer to create a high-converting, modern, and professional website design for a local plumbing company. The goal is to move away from the "dated" look of traditional trades and provide a seamless, trustworthy experience for homeowners and commercial clients.
The Challenge
Create a Homepage and a Service Page design that balances professional expertise with an urgent "call-to-action" (CTA) focus. We need a design that looks great on desktop but is built with a mobile-first mindset, as most customers find plumbers via their phones during emergencies.
This company will focus more on B2B, and corporate contracts, but should still be friendly to the public.
Here are some examples of what we are looking for
https://velotrin-works.com/construction/plumbing-construction/
https://velotrin-works.com/
The company is called "KT Plumbing."
Please see the logo below.

```html
<!DOCTYPE html>
<html lang="en">
<head>
<meta charset="utf-8">
<title>KT Plumbing — Commercial Plumbing</title>
<link rel="stylesheet" href="https://fonts.googleapis.com/css2?family=Montserrat:wght@400;500;600;700;800&family=Open+Sans:wght@400;600;700&family=Roboto:wght@500&display=swap">
<style>
:root{
  --ink:#0f1b26;
  --navy:#0e1a24;
  --footer:#10243a;
  --text:#6b6f74;
  --white:#ffffff;
}
*{margin:0;padding:0;box-sizing:border-box}
html,body{width:1200px;height:3770px;overflow:hidden;background:var(--white)}
body{position:relative;font-family:"Montserrat",sans-serif;color:var(--ink)}
.abs{position:absolute}

.site-header{position:absolute;left:0;top:0;width:1200px;height:69px;background:var(--white)}
.brand{position:absolute;left:111px;top:18px;display:flex;align-items:center;gap:10px;font-weight:800;font-size:25px;color:var(--ink);letter-spacing:.3px}
.brand-square{width:26px;height:26px;background:var(--ink)}
.main-nav{position:absolute;left:421px;top:24px;display:flex;gap:33px;font-size:13px;color:#333}
.main-nav a{color:inherit;text-decoration:none;position:relative}
.main-nav a.active{font-weight:700;color:var(--ink)}
.main-nav a.active::after{content:"";position:absolute;left:-2px;right:-2px;top:41px;height:5px;background:var(--ink)}
.btn-contact{position:absolute;left:988px;top:10px;width:99px;height:41px;background:var(--navy);color:var(--white);font-weight:700;font-size:13px;display:flex;align-items:center;justify-content:center;clip-path:polygon(6% 0,100% 0,94% 100%,0 100%)}

.btn-skew{display:flex;align-items:center;justify-content:center;font-weight:700;clip-path:polygon(5% 0,100% 0,95% 100%,0 100%)}
.btn-dark{background:var(--navy);color:var(--white)}
.btn-light{background:var(--white);color:var(--ink)}

.hero{position:absolute;left:0;top:69px;width:1200px;height:604px;background:linear-gradient(100deg,#dcdbd6 0%,#c9c8c3 45%,#9c9d9b 70%,#6f6c66 100%)}
.hero-title{position:absolute;left:110px;top:72px;font-size:47px;line-height:61px;font-weight:500;color:var(--ink)}
.hero-title strong{font-weight:800}
.hero-lead{position:absolute;left:110px;top:322px;width:400px;font-size:14px;line-height:28px;color:var(--ink)}
.hero-cta{position:absolute;left:114px;top:423px;width:199px;height:42px;font-size:13px}

.about-photo{position:absolute;left:111px;top:758px;width:446px;height:445px;border-radius:6px;background:linear-gradient(160deg,#e8e6e1 0%,#c7a08a 45%,#e0531e 75%,#d8d4ce 100%)}
.section-title{display:flex;align-items:center;gap:12px;font-size:44px;font-weight:500;color:var(--ink)}
.section-title strong{font-weight:800}
.title-square{width:36px;height:30px;background:var(--ink);clip-path:polygon(25% 0,100% 0,75% 100%,0 100%)}
.about-title{position:absolute;left:645px;top:762px}
.about-copy{position:absolute;left:648px;top:848px;width:442px;font-size:13px;line-height:31px;color:var(--text);text-align:justify}
.about-copy p+p{margin-top:12px}
.about-cta{position:absolute;left:645px;top:1135px;width:126px;height:41px;font-size:12px}

.services{position:absolute;left:0;top:1301px;width:1200px;height:551px}
.service-label{position:absolute;font-family:"Open Sans",sans-serif;font-weight:700;font-size:23px;color:var(--white)}
.service-center{position:absolute;left:480px;top:200px;width:300px;text-align:center;color:var(--white);font-family:"Open Sans",sans-serif}
.service-center h3{font-size:25px;font-weight:700}
.service-center p{font-size:15px;font-weight:600;line-height:29px;margin-top:14px}
.service-cta{position:absolute;left:550px;top:358px;width:123px;height:41px;font-size:13px;font-family:"Open Sans",sans-serif;font-weight:600}

.values-title{position:absolute;left:0;top:1935px;width:1200px;justify-content:center}
.value{position:absolute;top:2036px;width:225px}
.value-head{display:flex;align-items:center;gap:22px;height:64px}
.value-icon{width:64px;height:64px;border-radius:50%;background:var(--white);box-shadow:0 2px 12px rgba(0,0,0,.14);display:flex;align-items:center;justify-content:center;flex:none}
.value-icon.active{background:var(--ink)}
.value-head span{font-size:20px;font-weight:500;color:var(--ink)}
.value p{margin-top:26px;font-size:12px;line-height:23.5px;color:var(--text)}

.cta-banner{position:absolute;left:111px;top:2323px;width:977px;height:363px;border-radius:8px;background:linear-gradient(90deg,#2b2d31 0%,#4a3a36 35%,#3a3c40 65%,#26282b 100%);text-align:center;color:var(--white)}
.cta-banner h2{position:absolute;left:0;right:0;top:98px;font-size:42px;font-weight:800}
.cta-banner p{position:absolute;left:0;right:0;top:168px;font-size:15px;font-weight:700}
.cta-banner .btn-skew{position:absolute;left:395px;top:225px;width:187px;height:42px;font-size:13px;font-weight:600}

.projects-title{position:absolute;left:0;top:2773px;width:1200px;justify-content:center}
.project{position:absolute;border-radius:6px}
.project-caption{position:absolute;left:44px;bottom:22px;font-family:"Roboto",sans-serif;font-weight:500;font-size:26px;color:var(--white)}

.site-footer{position:absolute;left:0;top:3388px;width:1200px;height:382px;background:var(--footer);color:var(--white)}
.footer-brand{position:absolute;left:111px;top:78px;display:flex;align-items:center;gap:12px;font-weight:800;font-size:34px;color:var(--white)}
.footer-brand .brand-square{width:36px;height:36px;background:var(--white)}
.footer-about{position:absolute;left:111px;top:172px;width:290px;font-size:14px;line-height:26px}
.socials{position:absolute;left:118px;top:271px;display:flex;gap:6px}
.socials span{width:30px;height:30px;border-radius:50%;border:2px solid var(--white)}
.footer-col{position:absolute;top:100px}
.footer-col h4{font-size:19px;font-weight:600;margin-bottom:12px}
.footer-col ul{list-style:none}
.links-small li{font-size:13px;line-height:24px}
.links-med li{font-size:15px;line-height:30px}
.contact-row{display:flex;align-items:flex-start;gap:14px;font-size:15px;line-height:24px;margin-bottom:24px}
.contact-row svg{flex:none;margin-top:2px}
.footer-rule{position:absolute;left:111px;top:333px;width:977px;height:1px;background:rgba(255,255,255,.4)}
.copyright{position:absolute;left:0;right:0;top:345px;text-align:center;font-size:13px}
</style>
</head>
<body>

<header class="site-header">
  <div class="brand"><span class="brand-square"></span>KT PLUMBING</div>
  <nav class="main-nav">
    <a class="active">Home</a><a>KT Service</a><a>KT MEP</a><a>Projects</a><a>Careers</a><a>About</a><a>Blog</a>
  </nav>
  <a class="btn-contact">CONTACT</a>
</header>

<section class="hero" role="img" aria-label="Plumber in hard hat and safety vest tightening a flush valve with a pipe wrench">
  <h1 class="hero-title"><strong>Commercial<br>Plumbing</strong> Solutions<br>Built for Reliability &amp;<br>Scale</h1>
  <p class="hero-lead">Serving contractors, property managers, and businesses with dependable plumbing installation, repair, and maintenance services.</p>
  <a class="hero-cta btn-skew btn-dark">Request Service Call Now</a>
</section>

<div class="about-photo" role="img" aria-label="Worker in orange shirt and hard hat installing overhead copper pipes"></div>
<h2 class="section-title about-title"><span class="title-square"></span>About <strong>Us</strong></h2>
<div class="about-copy">
  <p>KT Plumbing is leading the evolution of construction. Each day we wake up and show up with a charge to fulfill our mission.</p>
  <p>KT Plumbing takes a big-picture approach to the construction process by self-performing electrical, HVAC, plumbing, process piping, underground utilities, prefabrication, and MEP design. Instead of multiple consultants and countless subcontractors, our customers work with just one company to eliminate profit layers, scope gaps, and complexity of schedules.</p>
</div>
<a class="about-cta btn-skew btn-dark">READ MORE</a>

<section class="services">
  <svg class="abs" width="1200" height="551" viewBox="0 0 1200 551">
    <defs>
      <linearGradient id="g1" x1="0" y1="0" x2="1" y2="1"><stop offset="0" stop-color="#d8d6d2"/><stop offset=".5" stop-color="#9a8f88"/><stop offset="1" stop-color="#3f3a37"/></linearGradient>
      <linearGradient id="g2" x1="0" y1="0" x2="1" y2="1"><stop offset="0" stop-color="#0f4a5e"/><stop offset="1" stop-color="#07222c"/></linearGradient>
      <linearGradient id="g3" x1="0" y1="0" x2="1" y2="1"><stop offset="0" stop-color="#e3e1dc"/><stop offset=".6" stop-color="#a7a39c"/><stop offset="1" stop-color="#5a5650"/></linearGradient>
    </defs>
    <polygon points="0,0 475,0 319,551 0,551" fill="url(#g1)" role="img" aria-label="Worker installing piping system"/>
    <polygon points="480,0 885,0 786,551 325,551" fill="url(#g2)" role="img" aria-label="Leak detection on a pipe valve"/>
    <polygon points="890,0 1200,0 1200,551 790,551" fill="url(#g3)" role="img" aria-label="Worker servicing a drinking fountain drain"/>
  </svg>
  <div class="service-label" style="left:31px;top:485px">SYSTEM INSTALLATION</div>
  <div class="service-center"><h3>LEAK DETECTION</h3><p>Advanced diagnostics to<br>identify hidden leaks.</p></div>
  <a class="service-cta btn-skew btn-light">READ MORE</a>
  <div class="service-label" style="left:913px;top:485px">DRAIN SYSTEMS</div>
</section>

<h2 class="section-title values-title"><span class="title-square"></span>Our <strong>Values</strong></h2>

<div class="value" style="left:111px">
  <div class="value-head"><div class="value-icon"><svg width="28" height="24" viewBox="0 0 28 24" fill="#0f1b26"><circle cx="14" cy="6" r="4.5"/><circle cx="5.5" cy="8" r="3.2"/><circle cx="22.5" cy="8" r="3.2"/><path d="M7 22c0-5 3-8 7-8s7 3 7 8z"/><path d="M0 20c0-4 2-7 5.5-7 1 0 2 .3 2.6.7C6.6 15.5 6 17.6 6 20z"/><path d="M28 20c0-4-2-7-5.5-7-1 0-2 .3-2.6.7 1.5 1.8 2.1 3.9 2.1 6.3z"/></svg></div><span>Teamwork</span></div>
  <p>Our people are the root of our success. We prioritize team over individual and understand collaboration is key to our success.</p>
</div>
<div class="value" style="left:367px">
  <div class="value-head"><div class="value-icon"><svg width="28" height="28" viewBox="0 0 28 28"><circle cx="14" cy="14" r="12" fill="#0f1b26"/><path d="M8 14l4 4 8-8" stroke="#fff" stroke-width="3" fill="none"/></svg></div><span>Excellence</span></div>
  <p>No matter what it is, from writing an email to installing equipment, we are committed to putting our whole hearts and minds into everything we do.</p>
</div>
<div class="value" style="left:623px">
  <div class="value-head"><div class="value-icon active"><svg width="28" height="28" viewBox="0 0 28 28" fill="none" stroke="#fff" stroke-width="2.5"><path d="M7 25V4"/><path d="M7 5h14l-3 5 3 5H7" fill="#fff"/></svg></div><span>Perseverance</span></div>
  <p>We have a never-give-up attitude. This comes from our willingness to problem-solve and our natural tendency to always look at the glass half full.</p>
</div>
<div class="value" style="left:879px">
  <div class="value-head"><div class="value-icon"><svg width="26" height="28" viewBox="0 0 26 28"><path d="M13 2l10 4v8c0 6-4 10-10 12C7 24 3 20 3 14V6z" fill="#0f1b26"/><path d="M9 14l3 3 5-6" stroke="#fff" stroke-width="2.5" fill="none"/></svg></div><span>Integrity</span></div>
  <p>We are individually and collectively accountable for our actions and expect honesty, openness, and transparency from our team.</p>
</div>

<section class="cta-banner" role="img" aria-label="Rows of prefabricated pipe assemblies in a workshop">
  <h2>Need Reliable Plumbing Support?</h2>
  <p>Our team is ready to assist with installations, maintenance, or emergency repairs.</p>
  <a class="btn-skew btn-light">CALL EMERGENCY LINE</a>
</section>

<h2 class="section-title projects-title"><span class="title-square"></span>Our <strong>Projects</strong></h2>
<div class="project" style="left:111px;top:2873px;width:444px;height:414px;background:linear-gradient(180deg,#6f8fb3 0%,#8a8a6e 40%,#a3876a 70%,#6d5a48 100%)" role="img" aria-label="Underground pipe risers on a job site with excavators">
  <div class="project-caption">Lorm Ipsum Dolor Siet</div>
</div>
<div class="project" style="left:579px;top:2873px;width:218px;height:202px;background:linear-gradient(160deg,#b9b4ad,#d7693b 55%,#8a7f76)" role="img" aria-label="Worker fitting copper pipes overhead"></div>
<div class="project" style="left:810px;top:2873px;width:278px;height:202px;background:linear-gradient(160deg,#d9d6d0,#b98a6a 50%,#e1b13a 80%)" role="img" aria-label="Worker brazing a copper pipe with a torch"></div>
<div class="project" style="left:579px;top:3087px;width:278px;height:202px;background:linear-gradient(160deg,#5f6e5b,#8fb23a 45%,#6b6a63)" role="img" aria-label="Worker kneeling to assemble pipe fittings"></div>
<div class="project" style="left:870px;top:3087px;width:218px;height:202px;background:linear-gradient(90deg,#c5c3bf,#b57a55 45%,#d4cfc8)" role="img" aria-label="Vertical copper pipes against a wall"></div>

<footer class="site-footer">
  <div class="footer-brand"><span class="brand-square"></span>KT PLUMBING</div>
  <p class="footer-about">Professional plumbing solutions for businesses, contractors, and property managers.</p>
  <div class="socials" aria-label="Social links"><span></span><span></span><span></span><span></span></div>

  <div class="footer-col" style="left:528px">
    <h4>Quick Links</h4>
    <ul class="links-small"><li>Home</li><li>KT Service</li><li>KT MEP</li><li>Projects</li><li>Careers</li><li>About</li><li>Blog</li></ul>
  </div>
  <div class="footer-col" style="left:702px">
    <h4>Other Links</h4>
    <ul class="links-med"><li>Privacy Policy</li><li>Terms &amp; Conditions</li><li>Disclaimer</li><li>Support</li><li>Help</li></ul>
  </div>
  <div class="footer-col" style="left:913px">
    <h4>Contact Info</h4>
    <div class="contact-row"><svg width="22" height="22" viewBox="0 0 22 22"><circle cx="11" cy="11" r="11" fill="#fff"/><path d="M11 5a4 4 0 0 0-4 4c0 3 4 8 4 8s4-5 4-8a4 4 0 0 0-4-4z" fill="#10243a"/><circle cx="11" cy="9" r="1.5" fill="#fff"/></svg><span>482 Corvane Street<br>Dellport, NV 89512</span></div>
    <div class="contact-row"><svg width="22" height="22" viewBox="0 0 22 22"><circle cx="11" cy="11" r="11" fill="#fff"/><path d="M7.5 6l2 .2 1 2.6-1.2 1a6 6 0 0 0 2.9 2.9l1-1.2 2.6 1 .2 2c-4.5.8-9.3-4-8.5-8.5z" fill="#10243a"/></svg><span>(555-204-7719</span></div>
    <div class="contact-row"><svg width="22" height="22" viewBox="0 0 22 22"><circle cx="11" cy="11" r="11" fill="#fff"/><rect x="5.5" y="7" width="11" height="8" rx="1" fill="#10243a"/><path d="M6 8l5 4 5-4" stroke="#fff" stroke-width="1.2" fill="none"/></svg><span>info@ktplumbing-co.com</span></div>
  </div>

  <div class="footer-rule"></div>
  <p class="copyright">© 2026 KT Plumbing Construction, Inc.</p>
</footer>

</body>
</html>
```